Business Card Design

Lark Haven Rentals
Lark Haven Rentals is a high end home rental leasing company that provides exquisite properties in niche markets. We are a small family owned business that considers our clients not as renters, but as friends. Every property we buy must be brought up to our high standards before it is offered on the market. The properties that we lease are exceptional, "move in" ready homes. This allows for the client to take pride in their lease as if it was their own home. To put it another way; we do not lease a property that we would not live in ourselves.

Target Market(s)

Couples making $100K or more

Industry/Entity Type

Business

Requirements
Must have
• Some sort of logo
Nice to have
• good slogan
Should not have
• Pink

```html
<!DOCTYPE html>
<html lang="en">
<head>
<meta charset="utf-8">
<title>Lark Haven Rentals – Business Card</title>
<link rel="stylesheet" href="https://fonts.googleapis.com/css2?family=Bree+Serif&family=Inter:wght@300;400&display=swap">
<style>
  :root {
    --sky: #6dcdf5;
    --lime: #cbdf5b;
    --ink: #5a5a5a;
    --paper: #ffffff;
  }
  html, body {
    margin: 0;
    padding: 0;
    width: 1200px;
    height: 704px;
    overflow: hidden;
    background: var(--paper);
  }
  .card {
    position: relative;
    width: 1200px;
    height: 704px;
    background: var(--paper);
    font-family: "Inter", Arial, sans-serif;
  }
  .brand-mark {
    position: absolute;
    left: 130px;
    top: 88px;
    width: 166px;
    height: 166px;
    background: var(--sky);
  }
  .brand-name {
    position: absolute;
    left: 317px;
    top: 120px;
    margin: 0;
    font-family: "Bree Serif", Georgia, serif;
    font-weight: 400;
    font-size: 53px;
    line-height: 1;
    color: var(--sky);
    white-space: nowrap;
  }
  .slogan {
    position: absolute;
    left: 317px;
    top: 186px;
    margin: 0;
    font-weight: 300;
    font-size: 29px;
    line-height: 1;
    color: var(--sky);
  }
  .contact {
    position: absolute;
    left: 524px;
    top: 286px;
    margin: 0;
    font-style: normal;
  }
  .contact-name {
    margin: 0 0 20px;
    font-weight: 400;
    font-size: 39px;
    line-height: 1;
    color: var(--sky);
    letter-spacing: 0.5px;
  }
  .contact-line {
    margin: 0 0 22px;
    font-weight: 300;
    font-size: 33px;
    line-height: 34px;
    color: var(--ink);
    white-space: nowrap;
  }
  .accent-band {
    position: absolute;
    left: 0;
    top: 548px;
    width: 1200px;
    height: 26px;
    background: var(--lime);
  }
  .footer-band {
    position: absolute;
    left: 0;
    top: 574px;
    width: 1200px;
    height: 130px;
    background: var(--sky);
  }
  .address {
    position: absolute;
    left: 130px;
    top: 622px;
    margin: 0;
    font-weight: 300;
    font-size: 31px;
    line-height: 1;
    color: var(--paper);
    letter-spacing: 0.5px;
    white-space: nowrap;
  }
</style>
</head>
<body>
  <main class="card">
    <div class="brand-mark"></div>
    <h1 class="brand-name">LarkHavenRentals</h1>
    <p class="slogan">Your next dream house</p>

    <address class="contact">
      <p class="contact-name">MARLOWE</p>
      <p class="contact-line">General Manager</p>
      <p class="contact-line">+1 555 0148 392</p>
      <p class="contact-line">marketing@larkhavenrentals.com</p>
    </address>

    <div class="accent-band"></div>
    <div class="footer-band"></div>
    <p class="address">18 Alder Lane, Suite 210. Brookfield, NY 10520. Code Post</p>
  </main>
</body>
</html>
```